Quillmere Capital LLC

Need Professional Business cards for New Investment Fund

Target Market(s)

High Quality investors

Industry/Entity Type

Financial

Contact Information for Business Card

Phone Number +1 555 284 6190
Name Lukas Varenko
Title Fund Manager
email lv@FundQuillmere.com
Website www.FundQuillmere.com

Colors

Designer to choose colors to be used in the design.

Requirements
Must have
• Must have our Logo and all of the above. Must be made so lettering and loge can be raised

```html
<!DOCTYPE html>
<html lang="en">
<head>
<meta charset="utf-8">
<title>Quillmere Capital LLC – Business Card</title>
<link href="https://fonts.googleapis.com/css2?family=Open+Sans:wght@400;600&display=swap" rel="stylesheet">
<style>
  :root {
    --backdrop: #3b322d;
    --card: #1e2022;
    --card-edge: #17191a;
    --accent: #33e32a;
    --accent-deep: #1f9a1c;
    --slate: #4a5048;
    --text-light: #e9ece8;
    --text-muted: #8b8f8c;
    --divider: #4a4d4f;
  }
  * { margin: 0; padding: 0; box-sizing: border-box; }
  html, body {
    width: 1200px; height: 864px; overflow: hidden;
    background: var(--backdrop);
    font-family: "Open Sans", Arial, sans-serif;
  }
  .canvas { position: relative; width: 1200px; height: 864px; }

  .card {
    position: absolute;
    width: 560px; height: 320px;
    background: var(--card);
    box-shadow: 0 6px 0 var(--card-edge), 0 16px 30px rgba(0,0,0,.45);
    overflow: hidden;
  }
  .card--front { left: 50px; top: 90px; }
  .card--back  { left: 590px; top: 440px; }

  /* Front: brand name only */
  .front-brand {
    position: absolute; left: 0; right: 0; top: 50%;
    transform: translateY(-50%);
    text-align: center;
  }
  .front-brand__name {
    font-weight: 600; font-size: 34px; letter-spacing: 5px;
    color: var(--accent-deep); text-transform: uppercase;
  }

  /* Back: bands */
  .band { position: absolute; height: 16px; background: var(--accent); }
  .band--top { top: 0; left: 40px; right: 0; }
  .band--bottom { bottom: 0; left: 0; right: 40px; }
  .band-cap { position: absolute; width: 40px; height: 16px; background: var(--slate); }
  .band-cap--top { top: 0; left: 0; }
  .band-cap--bottom { bottom: 0; right: 0; }

  .back-brand {
    position: absolute; left: 30px; top: 136px; width: 210px;
    display: flex; align-items: center; gap: 8px;
  }
  .back-brand__mark { width: 12px; height: 12px; background: var(--accent); flex: none; }
  .back-brand__name {
    font-weight: 600; font-size: 20px; letter-spacing: 2px;
    color: var(--accent); text-transform: uppercase; white-space: nowrap;
  }

  .divider {
    position: absolute; left: 250px; top: 80px;
    width: 1px; height: 160px; background: var(--divider);
  }

  .contact { position: absolute; left: 275px; top: 92px; }
  .contact__name {
    font-weight: 600; font-size: 20px; color: var(--accent);
    text-transform: uppercase; letter-spacing: .5px;
  }
  .contact__title {
    font-weight: 600; font-size: 14px; color: var(--text-light);
    margin-bottom: 14px;
  }
  .contact__row {
    display: flex; align-items: center; gap: 10px;
    font-size: 14px; color: var(--text-muted); line-height: 22px;
    white-space: nowrap;
  }
  .contact__row svg { width: 12px; height: 12px; flex: none; fill: var(--accent); }
</style>
</head>
<body>
<main class="canvas">
  <section class="card card--front" aria-label="Card front">
    <div class="front-brand">
      <p class="front-brand__name">Quillmere</p>
    </div>
  </section>

  <section class="card card--back" aria-label="Card back">
    <span class="band-cap band-cap--top"></span>
    <span class="band band--top"></span>
    <span class="band band--bottom"></span>
    <span class="band-cap band-cap--bottom"></span>

    <div class="back-brand">
      <span class="back-brand__mark"></span>
      <span class="back-brand__name">Quillmere</span>
    </div>

    <span class="divider"></span>

    <div class="contact">
      <p class="contact__name">Lukas Varenko</p>
      <p class="contact__title">Fund Manager</p>
      <p class="contact__row">
        <svg viewBox="0 0 12 12" aria-hidden="true"><path d="M2 1h2l1 3-1.5 1a7 7 0 0 0 3.5 3.5L8 7l3 1v2a1 1 0 0 1-1 1A9 9 0 0 1 1 2a1 1 0 0 1 1-1z"/></svg>
        +1 555 284 6190
      </p>
      <p class="contact__row">
        <svg viewBox="0 0 12 12" aria-hidden="true"><path d="M0 2h12v1L6 7 0 3zM0 4.5l6 4 6-4V10H0z"/></svg>
        lv@FundQuillmere.com
      </p>
      <p class="contact__row">
        <svg viewBox="0 0 12 12" aria-hidden="true"><circle cx="6" cy="6" r="6"/><circle cx="6" cy="6" r="2.2" fill="#1e2022"/></svg>
        www.FundQuillmere.com
      </p>
    </div>
  </section>
</main>
</body>
</html>
```